Flyer for tutoring

The text should be presented in an engaging way to attract potential customers.
Colorfully designed
Around the edge, various objects related to school and the subjects (see text) should be visible.

```html
<!DOCTYPE html>
<html lang="de">
<head>
<meta charset="utf-8">
<title>Nachhilfe – Lena Hofmann</title>
<link rel="stylesheet" href="https://fonts.googleapis.com/css2?family=Fredoka:wght@500;600;700&family=Dancing+Script:wght@700&family=Itim&family=Neucha&display=swap">
<style>
  :root {
    --navy: #2d4f84;
    --blue-band: #2f5a93;
    --orange: #e8862f;
    --orange-dark: #d9752a;
    --red: #c23a30;
    --green: #76b82a;
    --check: #6cbf2a;
    --box: #d3e3ad;
    --ink: #1f2430;
    --paper-top: #f4f7fb;
    --paper-mid: #eaf1f9;
  }
  * { margin: 0; padding: 0; box-sizing: border-box; }
  html, body { width: 848px; height: 1200px; overflow: hidden; background: #fff; }
  .flyer {
    position: relative; width: 848px; height: 1200px; overflow: hidden;
    background: radial-gradient(ellipse at 50% 45%, #ffffff 0%, var(--paper-top) 55%, var(--paper-mid) 100%);
    font-family: "Itim", "Comic Sans MS", sans-serif; color: var(--navy);
  }
  .deco { position: absolute; border-radius: 18px; }
  .abs { position: absolute; }

  .band { position: absolute; }
  .band-text {
    position: absolute; left: 0; right: 0; text-align: center;
    font-family: "Fredoka", sans-serif; font-weight: 600; color: #fff; letter-spacing: .5px;
  }
  .headline-1 { top: 67px; left: 168px; width: 519px; height: 52px; }
  .headline-1 .band-text { top: 3px; font-size: 35px; }
  .headline-2 { top: 123px; left: 168px; width: 536px; height: 52px; }
  .headline-2 .band-text { top: 5px; font-size: 35px; }

  .tagline-rule { position: absolute; top: 203px; height: 2px; background: var(--navy); }
  .tagline {
    position: absolute; top: 180px; left: 333px; width: 209px; text-align: center;
    font-family: "Dancing Script", cursive; font-size: 36px; color: var(--navy);
  }
  .role {
    position: absolute; left: 140px; width: 580px; text-align: center;
    font-family: "Fredoka", sans-serif; font-weight: 700; line-height: 1;
  }
  .role-main { top: 232px; font-size: 47px; color: var(--red); }
  .role-sub { top: 279px; font-size: 47px; color: var(--orange); }
  .role-note { position: absolute; top: 322px; left: 140px; width: 580px; text-align: center; font-size: 18px; }

  .offer-badge { position: absolute; left: 624px; top: 262px; width: 168px; height: 100px; transform: rotate(14deg); }
  .offer-badge svg { position: absolute; inset: 0; }
  .offer-badge .b-title { position: absolute; top: 8px; left: 0; right: 0; text-align: center; font-family: "Fredoka", sans-serif; font-weight: 600; font-size: 14px; line-height: 1.05; color: #fff; }
  .offer-badge .b-note { position: absolute; top: 58px; left: 0; right: 0; text-align: center; font-size: 10px; line-height: 1.2; color: #fff; }

  .benefits { position: absolute; font-size: 20px; color: var(--navy); }
  .benefits li { list-style: none; position: absolute; white-space: nowrap; padding-left: 37px; line-height: 24px; }
  .benefits svg { position: absolute; left: 0; top: 2px; }

  .about-box { position: absolute; left: 133px; top: 497px; width: 577px; height: 243px; background: var(--box); border-radius: 30px; }
  .about-band { top: 471px; left: 212px; width: 403px; height: 58px; }
  .about-band .band-text { top: 5px; font-size: 38px; font-weight: 700; }
  .about-text { position: absolute; left: 145px; top: 554px; width: 555px; font-size: 14.5px; line-height: 24px; color: var(--navy); }
  .subjects-title { position: absolute; left: 145px; top: 604px; font-size: 27px; color: var(--navy); }
  .subject { position: absolute; font-size: 19px; color: var(--navy); white-space: nowrap; line-height: 24px; }
  .subject-icon { position: absolute; border-radius: 5px; }

  .steps-title { position: absolute; left: 184px; top: 758px; font-family: "Fredoka", sans-serif; font-weight: 600; font-size: 24px; color: var(--ink); }
  .steps { position: absolute; left: 209px; top: 790px; font-size: 19px; color: var(--navy); list-style: none; }
  .steps li { position: relative; padding-left: 14px; line-height: 31px; }
  .steps li::before { content: ""; position: absolute; left: 0; top: 14px; width: 4px; height: 4px; border-radius: 50%; background: var(--navy); }

  .contact-rule { position: absolute; top: 968px; height: 2px; background: var(--orange); }
  .contact-title { position: absolute; top: 948px; left: 338px; width: 212px; text-align: center; font-family: "Fredoka", sans-serif; font-weight: 600; font-size: 33px; color: var(--orange); }
  .contact-name { position: absolute; top: 996px; left: 0; width: 848px; text-align: center; font-size: 19px; color: var(--navy); }
  .contact-line { position: absolute; left: 0; width: 848px; text-align: center; font-family: "Neucha", cursive; font-size: 26px; color: var(--navy); }
</style>
</head>
<body>
<main class="flyer">

  <!-- border decorations -->
  <div class="deco" role="img" aria-label="Illustration: Glühbirne und Bleistifte" style="left:0;top:36px;width:150px;height:110px;background:radial-gradient(circle at 30% 40%,#f6d25a,#f3e3b0 55%,transparent 75%);"></div>
  <div class="deco" role="img" aria-label="Illustration: Bleistift" style="left:0;top:150px;width:100px;height:80px;background:linear-gradient(160deg,transparent 30%,#f0a63c 50%,transparent 70%);"></div>
  <div class="deco" role="img" aria-label="Illustration: Globus" style="left:0;top:213px;width:96px;height:180px;background:radial-gradient(circle at 40% 40%,#4a9fd6,#a7cf7a 45%,#d99544 70%,transparent 80%);"></div>
  <div class="deco" role="img" aria-label="Illustration: Bleistift und Ringbuch" style="left:0;top:420px;width:95px;height:188px;background:linear-gradient(180deg,#a9d27e 0%,#f4efe2 30%,#eee6d4 100%);"></div>
  <div class="deco" role="img" aria-label="Illustration: roter Bleistift" style="left:0;top:613px;width:48px;height:122px;background:linear-gradient(200deg,#f2c08a,#e46c4a 60%,transparent);"></div>
  <div class="deco" role="img" aria-label="Illustration: Notizblock mit Bleistift" style="left:0;top:764px;width:96px;height:166px;background:linear-gradient(180deg,#f4efe2,#4d8fc9 90%);"></div>
  <div class="deco" role="img" aria-label="Illustration: Schulrucksack" style="left:0;top:955px;width:142px;height:170px;background:radial-gradient(circle at 45% 50%,#f0a43f 0%,#3b9bb0 40%,#2f7f96 70%,transparent 85%);"></div>
  <div class="deco" role="img" aria-label="Illustration: offenes Heft mit Bleistift" style="left:29px;top:1094px;width:268px;height:106px;background:linear-gradient(170deg,#f7f3ea,#ece3cf 70%,#f1a54a);"></div>
  <div class="deco" role="img" aria-label="Illustration: Radiergummi" style="left:316px;top:1126px;width:88px;height:46px;background:linear-gradient(90deg,#f3f3f3,#3d78c0);"></div>
  <div class="deco" role="img" aria-label="Illustration: Radiergummi in Frankreichfarben" style="left:493px;top:1094px;width:92px;height:58px;background:linear-gradient(90deg,#2e5fb3 33%,#f6f6f6 33% 66%,#d9453d 66%);"></div>
  <div class="deco" role="img" aria-label="Illustration: Bücherstapel mit Schriftrolle" style="left:606px;top:956px;width:242px;height:244px;background:linear-gradient(170deg,transparent 5%,#d94a3b 15%,#2f5fa6 35%,#f4ede0 50%,#2f5fa6 65%,#e2a754 80%,#c9563a 100%);"></div>
  <div class="deco" role="img" aria-label="Illustration: Wecker" style="left:707px;top:45px;width:116px;height:136px;background:radial-gradient(circle at 50% 55%,#fdf5e6 0%,#fdf5e6 35%,#e8752c 50%,transparent 70%);"></div>
  <div class="deco" role="img" aria-label="Illustration: Flagge Grossbritannien" style="left:751px;top:204px;width:75px;height:55px;background:linear-gradient(135deg,#2a4a8f,#ffffff 50%,#c9353a);border-radius:6px;"></div>
  <div class="deco" role="img" aria-label="Illustration: Buntstifte" style="left:788px;top:270px;width:60px;height:100px;background:linear-gradient(200deg,#7cbf4a,#4f8fd0 60%,transparent);"></div>
  <div class="deco" role="img" aria-label="Illustration: Taschenrechner" style="left:784px;top:563px;width:64px;height:114px;background:linear-gradient(160deg,#e6533a,#f07a4a);"></div>
  <div class="deco" role="img" aria-label="Illustration: Lupe" style="left:768px;top:688px;width:80px;height:90px;background:radial-gradient(circle at 35% 35%,#cfe6f4,#7aa6c8 45%,#4d9a45 70%,transparent 80%);"></div>
  <div class="deco" role="img" aria-label="Illustration: Säulenkapitell" style="left:765px;top:766px;width:70px;height:70px;background:radial-gradient(circle,#f1d79a,#e2b85e 60%,transparent 80%);"></div>
  <div class="deco" role="img" aria-label="Illustration: Büroklammer" style="left:770px;top:880px;width:70px;height:50px;background:radial-gradient(ellipse,#f0b7d8,transparent 70%);"></div>

  <!-- headline -->
  <div class="band headline-1">
    <svg width="519" height="52" viewBox="0 0 519 52" aria-hidden="true"><path d="M6 4 L512 0 L519 10 L510 20 L517 34 L508 48 L12 52 L0 42 L10 30 L2 18 Z" fill="var(--blue-band)"/></svg>
    <div class="band-text">WILLST DU DICH IN DER</div>
  </div>
  <div class="band headline-2">
    <svg width="536" height="52" viewBox="0 0 536 52" aria-hidden="true"><path d="M10 2 L528 6 L536 18 L526 28 L534 44 L14 50 L4 40 L12 28 L0 14 Z" fill="var(--orange)"/></svg>
    <div class="band-text">SCHULE VERBESSERN?</div>
  </div>

  <div class="tagline-rule" style="left:177px;width:156px;"></div>
  <div class="tagline">professionelle</div>
  <div class="tagline-rule" style="left:542px;width:156px;"></div>

  <h1 class="role role-main">NACHHILFELEHRERIN</h1>
  <div class="role role-sub">&amp; LERNCOACH</div>
  <p class="role-note">auch für Kleingruppen möglich</p>

  <div class="offer-badge">
    <svg width="168" height="100" viewBox="0 0 168 100" aria-hidden="true">
      <path d="M18 6 Q84 -4 150 6 Q166 20 160 50 Q168 80 150 94 Q84 104 18 94 Q0 80 8 50 Q0 20 18 6 Z" fill="var(--orange-dark)"/>
      <line x1="22" y1="52" x2="146" y2="52" stroke="#fff" stroke-width="1"/>
    </svg>
    <div class="b-title">ERSTE LEKTION<br>KOSTENLOS</div>
    <div class="b-note">(30 Minuten<br>Kennenlernlektion)</div>
  </div>

  <ul class="benefits">
    <li style="left:154px;top:366px;"><svg width="22" height="22" viewBox="0 0 22 22"><circle cx="11" cy="11" r="10" fill="var(--check)"/><path d="M6 11.5 L9.5 15 L16 8" stroke="#fff" stroke-width="2.4" fill="none" stroke-linecap="round" stroke-linejoin="round"/></svg>Mehr Motivation</li>
    <li style="left:154px;top:397px;"><svg width="22" height="22" viewBox="0 0 22 22"><circle cx="11" cy="11" r="10" fill="var(--check)"/><path d="M6 11.5 L9.5 15 L16 8" stroke="#fff" stroke-width="2.4" fill="none" stroke-linecap="round" stroke-linejoin="round"/></svg>Bessere Noten</li>
    <li style="left:154px;top:428px;"><svg width="22" height="22" viewBox="0 0 22 22"><circle cx="11" cy="11" r="10" fill="var(--check)"/><path d="M6 11.5 L9.5 15 L16 8" stroke="#fff" stroke-width="2.4" fill="none" stroke-linecap="round" stroke-linejoin="round"/></svg>Individuelle Betreuung</li>
    <li style="left:407px;top:367px;"><svg width="22" height="22" viewBox="0 0 22 22"><circle cx="11" cy="11" r="10" fill="var(--check)"/><path d="M6 11.5 L9.5 15 L16 8" stroke="#fff" stroke-width="2.4" fill="none" stroke-linecap="round" stroke-linejoin="round"/></svg>Strukturierte Lernmethoden</li>
    <li style="left:407px;top:400px;"><svg width="22" height="22" viewBox="0 0 22 22"><circle cx="11" cy="11" r="10" fill="var(--check)"/><path d="M6 11.5 L9.5 15 L16 8" stroke="#fff" stroke-width="2.4" fill="none" stroke-linecap="round" stroke-linejoin="round"/></svg>Unterstützung bei Prüfungen</li>
  </ul>

  <!-- about -->
  <section>
    <div class="about-box"></div>
    <div class="band about-band">
      <svg width="403" height="58" viewBox="0 0 403 58" aria-hidden="true"><path d="M14 6 L396 0 L403 14 L392 26 L400 40 L386 54 L22 58 L12 46 L20 36 L0 24 L16 14 Z" fill="var(--green)"/></svg>
      <h2 class="band-text">ÜBER MICH</h2>
    </div>
    <p class="about-text">Ich wohne in der Siedlung Lindenweg und bin ausgebildete, sehr erfahrene Sekundar- und Primarlehrerin.</p>
    <h3 class="subjects-title">Fächer:</h3>

    <div class="subject-icon" role="img" aria-label="Icon: Buch mit Deutschlandflagge" style="left:150px;top:660px;width:34px;height:24px;background:linear-gradient(180deg,#333 33%,#d33 33% 66%,#f2c230 66%);"></div>
    <div class="subject" style="left:193px;top:660px;">Deutsch</div>
    <div class="subject-icon" role="img" aria-label="Icon: Eiffelturm und Buch" style="left:150px;top:688px;width:36px;height:26px;background:linear-gradient(90deg,#6b7fa0,#3d6cc0 50%,#e05a5a);"></div>
    <div class="subject" style="left:193px;top:689px;">Französisch</div>

    <div class="subject-icon" role="img" aria-label="Icon: Sprechblase ABC" style="left:367px;top:657px;width:30px;height:22px;background:#3d78d0;border-radius:50%;"></div>
    <div class="subject" style="left:414px;top:660px;">Englisch</div>
    <div class="subject-icon" role="img" aria-label="Icon: Säule und Schriftrolle" style="left:366px;top:688px;width:40px;height:24px;background:linear-gradient(90deg,#e2b85e,#f0dfb0);"></div>
    <div class="subject" style="left:414px;top:689px;">Geschichte</div>

    <div class="subject-icon" role="img" aria-label="Icon: Taschenrechner mit Rechenzeichen" style="left:528px;top:664px;width:38px;height:22px;background:linear-gradient(90deg,#3d78d0 40%,#f0a03c);"></div>
    <div class="subject" style="left:575px;top:657px;">Mathe (auf<br>Wunsch)</div>
  </section>

  <!-- process -->
  <section>
    <h3 class="steps-title">ABLAUF</h3>
    <ul class="steps">
      <li>Kostenlose Kennenlernlektion (ca. 30 Minuten)</li>
      <li>Gemeinsame Zieldefinition</li>
      <li>Individueller Lernplan</li>
      <li>Regelmässige Unterstützung, Fortschrittskontrolle<br>und Rückmeldung an die Eltern</li>
    </ul>
  </section>

  <!-- contact -->
  <section>
    <div class="contact-rule" style="left:207px;width:140px;"></div>
    <h3 class="contact-title">KONTAKT</h3>
    <div class="contact-rule" style="left:537px;width:140px;"></div>
    <p class="contact-name">Lena Hofmann</p>
    <p class="contact-line" style="top:1024px;">lena.hofmann@beispielpost.ch</p>
    <p class="contact-line" style="top:1055px;">076&nbsp;&nbsp;123&nbsp;&nbsp;45&nbsp;&nbsp;67</p>
  </section>

</main>
</body>
</html>
```